A parent Company needs a website as a leading diversified business in industrial Conglomerates in Af

Velkor Group is a private (Holding) limited liability company incorporated under the Companies Code, 1963 (Act 179) in November, 2013 to following the speedy growth in numbers of its current subsidiaries which has been founded several years ago with an emerging force to become one of the largest and a leading diversified business in industrial Conglomerates in Africa.
The Group which is 100% wholly owned indigenous Ghanaian Company focuses on provision of local, value-added products and services that meet the needs of the African population. The Group is headquartered in Accra, Ghana with interests across a range of sectors in Africa.
We are currently into Food & Beverage, Real Estate Development, Transportation, Health Care, Consumer Products Distribution, Agro Processing, Manufacturing, ICT, Exports & Import, and still counting.
In the next 3 years, we shall announce our ambitions to enter Ghana's largest Oil and Gas industry, playing a strategic role in the petroleum sector with strategic alliances, and help build Ghana's biggest and most important Energy sector in the country.
Inspired by billionaires Tom Prewitt, Harlan Voskel, and Emeka Ofodile, Velkor Group (Velkor Foundation) is committed to making a name for itself on the philanthropic circuit and has given away privately and still given to the cause to the needy in the society and some specific social causes in Ghana.
The company is managed by a 5 member board and a 2 member advisory experts who are non-board members.
The company has a vision, mission and it is guided by its core values.
We would like to see a designs that is very professional and looks corporate and can attract investors and partners. It must communicate financial safety and growth and must reflect our logo colors.

```html
<!DOCTYPE html>
<html lang="en">
<head>
<meta charset="utf-8">
<title>Velkor Group</title>
<link href="https://fonts.googleapis.com/css2?family=Ubuntu:wght@400;500;700&family=Open+Sans:wght@400;600&display=swap" rel="stylesheet">
<style>
:root{
  --blue:#29a9e0;
  --orange:#f28a14;
  --dark:#1f1f1f;
  --panel:#333333;
  --text:#444444;
  --white:#ffffff;
  --hero-a:#1c2a3a;
  --hero-b:#5a6a78;
}
*{margin:0;padding:0;box-sizing:border-box}
html,body{width:750px;height:1200px;overflow:hidden;background:var(--white)}
body{position:relative;font-family:"Open Sans",sans-serif;color:var(--text)}
.abs{position:absolute}
.hero-photo{left:0;top:0;width:750px;height:412px;background:linear-gradient(120deg,var(--hero-a) 0%,#34495c 45%,var(--hero-b) 75%,#7c8a6a 100%)}
.hero-cut{left:0;top:0}
.topbar{left:54px;top:0;width:612px;height:70px;background:rgba(255,255,255,.93);box-shadow:0 2px 6px rgba(0,0,0,.3)}
.brand{left:16px;top:22px;display:flex;align-items:center;gap:7px;font-family:"Ubuntu",sans-serif;font-size:14px;font-weight:500;color:#1d3f7a}
.brand-dot{width:14px;height:14px;border-radius:50%;background:var(--blue)}
.social-top{right:26px;top:8px;display:flex;gap:4px}
.social-top span{width:21px;height:21px;border-radius:50%;border:1px solid #bbb;background:#f4f4f4}
.nav a{position:absolute;top:43px;font-family:"Ubuntu",sans-serif;font-size:8.5px;line-height:10px;color:#222;text-decoration:none;white-space:nowrap}
.nav a.active{top:39px;padding:4px 9px;background:#1a1a1a;color:var(--white);border-radius:2px}
.hero-title{left:69px;top:120px;font-family:"Ubuntu",sans-serif;font-weight:700;font-size:30px;color:var(--blue)}
.hero-text{left:69px;top:170px;width:270px;font-size:9.4px;line-height:12.6px;color:var(--white)}
.hero-btn{left:74px;top:249px;width:180px;height:45px;background:linear-gradient(#fff,#e6e6e6);border-radius:3px;box-shadow:0 2px 4px rgba(0,0,0,.35)}
.hero-btn .ic{position:absolute;left:-3px;top:10px;width:28px;height:26px;background:var(--orange);border-radius:2px}
.hero-btn .lbl{position:absolute;left:40px;top:7px;width:110px;text-align:center;font-family:"Ubuntu",sans-serif;font-weight:500;font-size:11.5px;line-height:16px;color:#333}
.dots{left:106px;top:362px;display:flex;gap:6px}
.dots span{width:20px;height:24px;border-radius:0 0 10px 10px;background:#ddd;position:relative}
.dots span::after{content:"";position:absolute;left:5px;top:8px;width:10px;height:10px;border-radius:50%;background:#bbb}
.dots span.on{background:#111}
.dots span.on::after{background:#fff}
.welcome{left:69px;top:408px;font-family:"Ubuntu",sans-serif;font-weight:400;font-size:19px;color:#333}
.welcome b{font-weight:500;color:var(--blue)}
.intro{left:69px;top:434px;width:520px;font-size:8.1px;line-height:12.5px}
.divider{left:80px;top:508px;width:590px;height:14px;background:radial-gradient(ellipse at center top,rgba(0,0,0,.1),rgba(0,0,0,0) 70%)}
.service{top:540px;width:175px}
.service h3{font-family:"Ubuntu",sans-serif;font-weight:400;font-size:13px;color:var(--blue);margin-top:12px}
.service .circ{position:absolute;right:0;top:2px;width:52px;height:52px;border-radius:50%;background:#ececec}
.service .circ svg{position:absolute;left:14px;top:14px}
.service p{margin-top:42px;font-size:7.6px;line-height:12px;color:#444}
.service .more{position:absolute;right:16px;top:170px;font-family:"Ubuntu",sans-serif;font-size:8.5px;color:#333;display:flex;align-items:center;gap:8px}
.service .more i{width:15px;height:15px;border-radius:50%;background:var(--orange);position:relative;box-shadow:0 0 0 2px #eee}
.service .more i::after{content:"";position:absolute;left:6px;top:4px;border-left:5px solid #fff;border-top:3.5px solid transparent;border-bottom:3.5px solid transparent}
.sec-title{font-family:"Ubuntu",sans-serif;font-weight:400;font-size:13px;color:var(--blue)}
.rule{height:2px;border-top:1px dashed #ccc}
.rule::before{content:"";display:block;width:26px;height:2px;background:var(--orange);margin-top:-1px}
.card{top:809px;width:142px;height:109px;border:1px solid #ddd;background:#fff;text-align:center}
.card .ph{height:78px}
.card h4{font-family:"Ubuntu",sans-serif;font-weight:400;font-size:9.5px;color:#222;margin-top:3px}
.card small{display:block;font-size:7px;color:#444;margin-top:1px}
.field{left:540px;width:141px;border:1px solid #ccc;background:#fff;font-size:6.5px;font-style:italic;color:#555;padding:4px 7px;box-shadow:inset 0 1px 2px rgba(0,0,0,.12)}
.submit{left:637px;top:902px;width:44px;height:17px;background:var(--orange);color:#fff;font-family:"Ubuntu",sans-serif;font-size:8px;text-align:center;line-height:17px}
.footer-bg{left:0;top:0}
.view-btn{left:538px;top:962px;width:120px;height:60px;border-radius:60px 60px 0 0;background:var(--orange)}
.view-lbl{left:554px;top:992px;font-family:"Ubuntu",sans-serif;font-weight:500;font-size:11.5px;color:#fff;transform:rotate(5deg)}
.f-head{font-family:"Ubuntu",sans-serif;font-weight:500;font-size:15px;color:#fff;display:flex;align-items:center;gap:9px}
.f-links{left:80px;top:1038px;list-style:none;font-size:8.5px;line-height:12px;color:#aaa}
.f-about{left:230px;top:1038px;width:148px;font-size:8px;line-height:12px;color:#ccc}
.f-social{left:232px;top:1104px;display:flex;gap:5px}
.f-social span{width:15px;height:15px;border-radius:3px;background:#5a7fc2}
.contact{left:406px;top:1062px;width:280px;height:110px;background:var(--panel);border-radius:6px}
.q-card{left:424px;top:1048px;width:74px;height:96px;background:#f2f2f2;border-radius:5px}
.q-lbl{left:417px;top:1153px;font-size:7.3px;color:#fff}
.q-lbl em{font-style:normal;color:var(--orange)}
.c-info{left:523px;top:1070px;font-size:8px;line-height:13px;color:#bbb}
.c-info h5{font-family:"Ubuntu",sans-serif;font-size:10.5px;font-weight:500;color:#fff;margin-bottom:4px}
.copy{left:70px;top:1162px;font-size:7px;color:#ccc}
</style>
</head>
<body>

<div class="abs hero-photo" role="img" aria-label="Photo of two engineers in hard hats reviewing plans at an industrial plant"></div>
<svg class="abs hero-cut" width="750" height="420" aria-hidden="true"><polygon points="0,334 750,412 750,420 0,420" fill="#fff"/></svg>

<header class="abs topbar">
  <div class="abs brand"><span class="brand-dot"></span>Velkor Group</div>
  <div class="abs social-top"><span></span><span></span><span></span><span></span><span></span></div>
  <nav class="nav">
    <a class="active" href="#" style="left:193px">Home</a>
    <a href="#" style="left:262px">Real Estate Development</a>
    <a href="#" style="left:391px">food</a>
    <a href="#" style="left:443px">Transportation</a>
    <a href="#" style="left:533px">Manufacturing</a>
  </nav>
</header>

<h1 class="abs hero-title">Manufacturing</h1>
<p class="abs hero-text">Velkor Group is a private (Holding) limited liability company incorporated under the Companies Code, 1963 (Act 179) in November, 2013 to following the speedy growth in numbers of its current subsidiaries.</p>
<div class="abs hero-btn">
  <span class="ic"><svg width="28" height="26"><polyline points="9,9 14,14 19,9" fill="none" stroke="#fff" stroke-width="2"/><polyline points="9,14 14,19 19,14" fill="none" stroke="#fff" stroke-width="2"/></svg></span>
  <span class="lbl">READ MORE<br>ABOUT</span>
  <svg style="position:absolute;right:-2px;bottom:-2px" width="26" height="22"><polygon points="26,0 26,22 0,22" fill="var(--orange)"/></svg>
</div>
<div class="abs dots"><span></span><span></span><span class="on"></span><span></span></div>

<h2 class="abs welcome">Welcome to <b>VELKOR GROUP</b></h2>
<p class="abs intro">Lorem Ipsum is simply dummy text of the printing and typesetting industry. Lorem Ipsum has been the industry's standard dummy text ever since the 1500s, when an unknown printer took a galley of type and scrambled it to make a type specimen book. It has survived not only five centuries, but also the leap into electronic typesetting, remaining essentially unchanged. It was popularised in the 1960s with the release of Tracmark sheets containing Lorem Ipsum passages, and more recently with desktop publishing software like Quillset Layout including versions of Lorem Ipsum.</p>
<div class="abs divider"></div>

<section class="abs service" style="left:69px">
  <h3>Food</h3>
  <div class="circ"><svg width="24" height="24"><rect x="4" y="1" width="2" height="22" fill="var(--orange)"/><rect x="1" y="1" width="8" height="9" rx="2" fill="none" stroke="var(--orange)" stroke-width="2"/><rect x="15" y="1" width="6" height="22" rx="3" fill="var(--orange)"/></svg></div>
  <p>Low pressure grout injection can fill cavities beneath slabs. By increasing pumping pressure, driveways, sidewalks, and floor slabs can be raised. This work is accomplished by utilizing special equipment to pump grout beneath the slab. High pressure compaction grouting can be utilized to densify or compact the sub-grade to overcome</p>
  <div class="more">Read More <i></i></div>
</section>
<section class="abs service" style="left:285px">
  <h3>Transportation</h3>
  <div class="circ"><svg width="24" height="24"><rect x="0" y="5" width="15" height="11" fill="var(--orange)"/><polygon points="16,8 21,8 24,12 24,16 16,16" fill="var(--orange)"/><circle cx="5" cy="18" r="3" fill="var(--orange)"/><circle cx="19" cy="18" r="3" fill="var(--orange)"/></svg></div>
  <p>Low pressure grout injection can fill cavities beneath slabs. By increasing pumping pressure, driveways, sidewalks, and floor slabs can be raised. This work is accomplished by utilizing special equipment to pump grout beneath the slab. High pressure compaction grouting can be utilized to densify or compact the sub-grade to overcome</p>
  <div class="more">Read More <i></i></div>
</section>
<section class="abs service" style="left:499px">
  <h3>Manufacturing</h3>
  <div class="circ"><svg width="24" height="24"><polygon points="0,22 0,6 3,6 3,2 6,2 6,12 12,8 12,12 18,8 18,12 24,8 24,22" fill="var(--orange)"/></svg></div>
  <p>Low pressure grout injection can fill cavities beneath slabs. By increasing pumping pressure, driveways, sidewalks, and floor slabs can be raised. This work is accomplished by utilizing special equipment to pump grout beneath the slab. High pressure compaction grouting can be utilized to densify or compact the sub-grade to overcome</p>
  <div class="more">Read More <i></i></div>
</section>

<h2 class="abs sec-title" style="left:69px;top:769px">Past Projects</h2>
<div class="abs rule" style="left:69px;top:790px;width:447px"></div>
<article class="abs card" style="left:70px"><div class="ph" role="img" aria-label="Photo of two engineers at an oil field" style="background:linear-gradient(#3c7cc0,#a8c4de 60%,#8a7a55)"></div><h4>Manufacturing</h4><small>de lettres</small></article>
<article class="abs card" style="left:222px"><div class="ph" role="img" aria-label="Photo of workers beside a pump jack" style="background:linear-gradient(#4a86c6,#b5cde2 55%,#7a6a4a)"></div><h4>Manufacturing</h4><small>de lettres</small></article>
<article class="abs card" style="left:375px"><div class="ph" role="img" aria-label="Photo of a pump jack on open land" style="background:linear-gradient(#7ea8cf,#dfe8ee 60%,#8a8f6a)"></div><h4>Manufacturing</h4><small>de lettres</small></article>

<h2 class="abs sec-title" style="left:540px;top:765px;font-size:13.5px;letter-spacing:.5px">PRIVATE ACCESS</h2>
<div class="abs rule" style="left:540px;top:790px;width:141px"></div>
<div class="abs field" style="top:810px;height:17px">Enter your name...</div>
<div class="abs field" style="top:833px;height:17px">Enter your email...</div>
<div class="abs field" style="top:855px;height:40px">Enter your comment...</div>
<div class="abs submit">Submit</div>

<div class="abs view-btn"></div>
<svg class="abs footer-bg" width="750" height="1200" aria-hidden="true"><polygon points="0,946 750,1024 750,1200 0,1200" fill="var(--dark)"/></svg>
<div class="abs view-lbl">VIEW PROJECTS</div>

<div class="abs f-head" style="left:78px;top:1013px"><svg width="20" height="16"><path d="M0 2h7l2 2h11v12H0z" fill="var(--orange)"/></svg>Links</div>
<ul class="abs f-links"><li>Home</li><li>Food</li><li>Real Estate Development</li><li>Transportation</li><li>Manufacturing</li></ul>
<div class="abs f-head" style="left:205px;top:1013px"><svg width="14" height="14"><rect y="1" width="14" height="3" fill="var(--orange)"/><rect y="6" width="14" height="3" fill="var(--orange)"/><rect y="11" width="14" height="3" fill="var(--orange)"/></svg>About Us</div>
<p class="abs f-about">Lorem Ipsum is simply dummy text of the printing and typesetting industry. Lorem Ipsum has been the industry's standard dummy text ever since the 1500s,</p>
<div class="abs f-social"><span></span><span></span><span style="background:#c8392e"></span><span style="background:#d44a3a"></span></div>

<div class="abs contact"></div>
<div class="abs q-card" role="img" aria-label="Illustration of a client questionnaire form"></div>
<p class="abs q-lbl"><em>Fill out our</em> Questionnaire</p>
<div class="abs c-info">
  <h5>Contact Info</h5>
  lorem Lispum<br>Dummy 106<br>Lipsum typesetting<br>Port Averly<br>Email: info@velkorgroup.com<br>Phone: NATIONWIDE 555-014-2290
</div>
<p class="abs copy">Copyright 2014 © Velkor Group All Rights Reserved</p>

</body>
</html>
```